A start up Private Wine Label for export to Asia.

We are looking for the best graphic design for our very first wine label Corvessa Wines and would like the following requirements:

1. Black background - explore and play around the shade of black
2. Gold Shimmery Colour Font
3. Font should be a cursive classic posh that says Corvessa Wines
4. We would like the front graphic design to be simple and elegant and has a traditional classic feel to it.

Target Market(s)

Small scale to test the upper class market for export to Asia

Font styles to use
Script

Colors

Designer to choose colors to be used in the design.

Requirements
Must have
• Gold font for the label Corvessa Wines with shimmery touch to it.
• Elegant black background.
• Simple but elegant design.
• Attractive to the upper class market in Asia.
Nice to have
• Explore and play around with your imagination.

```html
<!DOCTYPE html>
<html lang="en">
<head>
<meta charset="utf-8">
<title>Corvessa Wines – Front Label</title>
<link rel="stylesheet" href="https://fonts.googleapis.com/css2?family=Allura&family=Arimo:ital@1&display=swap">
<style>
  :root {
    --canvas: #ffffff;
    --label-black: #221f20;
    --gold-deep: #a9782b;
    --gold-mid: #d2a655;
    --gold-light: #f1dc8a;
    --gold-text: #c99a45;
    --glow-strong: rgba(241, 220, 138, 0.42);
    --glow-mid: rgba(210, 166, 85, 0.24);
    --glow-soft: rgba(169, 120, 43, 0.10);
    --edge-shadow: rgba(0, 0, 0, 0.25);
  }

  html, body {
    margin: 0;
    padding: 0;
    width: 1200px;
    height: 1200px;
    overflow: hidden;
    background: var(--canvas);
  }

  .wine-label {
    position: absolute;
    left: 206px;
    top: 50px;
    width: 788px;
    height: 1100px;
    box-sizing: border-box;
    padding: 32px 39px 33px;
    background: linear-gradient(90deg,
      var(--gold-deep) 0%, var(--gold-mid) 18%, var(--gold-light) 30%,
      var(--gold-mid) 45%, var(--gold-light) 60%, var(--gold-mid) 75%,
      var(--gold-light) 88%, var(--gold-deep) 100%);
    box-shadow: 0 2px 6px var(--edge-shadow);
  }

  .label-panel {
    position: relative;
    width: 100%;
    height: 100%;
    background: var(--label-black);
  }

  .sunburst {
    position: absolute;
    left: 23px;
    right: 23px;
    height: 373px;
    background-color: var(--label-black);
  }

  .sunburst--upper {
    top: 46px;
    background-image: radial-gradient(ellipse 70% 100% at 50% 100%,
      var(--glow-strong) 0%, var(--glow-mid) 40%, var(--glow-soft) 75%, transparent 100%);
  }

  .sunburst--lower {
    top: 614px;
    background-image: radial-gradient(ellipse 70% 100% at 50% 0%,
      var(--glow-strong) 0%, var(--glow-mid) 40%, var(--glow-soft) 75%, transparent 100%);
  }

  .name-band {
    position: absolute;
    left: 0;
    right: 0;
    top: 419px;
    height: 195px;
    background: var(--label-black);
    display: flex;
    align-items: center;
    justify-content: center;
  }

  .brand-name {
    margin: 0;
    font-family: "Allura", cursive;
    font-weight: 400;
    font-size: 124px;
    line-height: 1;
    color: var(--gold-text);
    white-space: nowrap;
  }

  .volume-line {
    position: absolute;
    left: 0;
    right: 0;
    top: 994px;
    margin: 0;
    text-align: center;
    font-family: "Arimo", sans-serif;
    font-style: italic;
    font-size: 38px;
    line-height: 1;
    color: var(--gold-mid);
  }
</style>
</head>
<body>
  <main class="wine-label">
    <div class="label-panel">
      <div class="sunburst sunburst--upper" role="img" aria-label="Gold sunburst rays on black radiating upward from the name band"></div>
      <div class="name-band">
        <h1 class="brand-name">Corvessa Wines</h1>
      </div>
      <div class="sunburst sunburst--lower" role="img" aria-label="Gold sunburst rays on black radiating downward from the name band"></div>
      <p class="volume-line">750 ml / ALC. 11% VOL</p>
    </div>
  </main>
</body>
</html>
```